Professional Photography Business cards

I need business cards that include my logo which I have uploaded. I run a photography business. I am open to ideas but I would like one side to have my logo and the other side to have my contact info. I don't have a website made but I do own a website domain. I have uploaded 2 different logo color schemes. My business colors are Blue, black , and white.

Business Name
Business Phone Number
Business Email
Business Website address
Instagram

Industry/Entity Type

Professional Photography

Contact Information for Business Card

Phone Number: 916-384-7702 email: info@tlane-studio.example Instagram: @t.lanestudio website doman- www.tlane-studio.example

Requirements
Must have
• I like the idea of a business card with a full black background front and back of card. My colors must include royal blue, black, and white

```html
<!DOCTYPE html>
<html lang="en">
<head>
<meta charset="utf-8">
<title>T. Lane Studio – Business Cards</title>
<link rel="stylesheet" href="https://fonts.googleapis.com/css2?family=Roboto:wght@400;500&display=swap">
<style>
  :root {
    --backdrop: #2b2422;
    --card-back: #151516;
    --card-front: #1d1d1f;
    --royal-blue: #1010b8;
    --white: #ffffff;
    --text-light: #ececec;
    --rule: #3a3a3c;
  }
  * { box-sizing: border-box; margin: 0; padding: 0; }
  html, body {
    width: 1200px; height: 842px; overflow: hidden;
    background: var(--backdrop);
    font-family: "Roboto", Arial, sans-serif;
  }
  .canvas {
    position: relative; width: 1200px; height: 842px;
    display: flex; align-items: center; justify-content: center; gap: 40px;
  }
  .card {
    position: relative; width: 540px; height: 309px; overflow: hidden;
    box-shadow: 0 18px 40px rgba(0,0,0,.55);
  }
  /* Contact side */
  .card--contact { background: var(--card-back); }
  .band { position: absolute; left: 0; width: 100%; background: var(--royal-blue); }
  .band--top { top: 0; height: 14px; }
  .band--bottom { bottom: 0; height: 14px; }
  .contact-body {
    position: absolute; inset: 14px 0; display: flex; flex-direction: column;
    align-items: center; justify-content: center;
  }
  .brand { display: flex; align-items: center; gap: 12px; }
  .brand__dot {
    width: 16px; height: 16px; border-radius: 50%; background: var(--royal-blue);
  }
  .brand__name {
    color: var(--white); font-weight: 500; letter-spacing: .22em; text-transform: uppercase;
  }
  .card--contact .brand { margin-bottom: 24px; }
  .card--contact .brand__name { font-size: 22px; }
  .contact-list { list-style: none; text-align: center; color: var(--text-light); font-size: 15px; line-height: 1.5; }
  .contact-list .accent { color: var(--royal-blue); }
  .contact-divider { width: 190px; height: 1px; background: var(--rule); margin: 8px 0 6px; }
  .social { font-size: 15px; color: var(--text-light); }
  .social .accent { color: var(--royal-blue); font-weight: 500; }
  /* Logo side */
  .card--logo { background: var(--card-front); }
  .edge-tab { position: absolute; width: 46px; height: 62px; background: var(--royal-blue); }
  .edge-tab::after {
    content: ""; position: absolute; top: 0; width: 4px; height: 100%; background: var(--white);
  }
  .edge-tab--left { left: 0; top: 150px; }
  .edge-tab--left::after { right: 0; }
  .edge-tab--right { right: 0; top: 52px; }
  .edge-tab--right::after { left: 0; }
  .logo-body { position: absolute; inset: 0; display: flex; align-items: center; justify-content: center; }
  .card--logo .brand__name { font-size: 30px; }
  .card--logo .brand__dot { width: 22px; height: 22px; }
</style>
</head>
<body>
<main class="canvas">
  <section class="card card--contact" aria-label="Contact side">
    <div class="band band--top"></div>
    <div class="band band--bottom"></div>
    <div class="contact-body">
      <div class="brand">
        <span class="brand__name">T. Lane Studio</span>
        <span class="brand__dot"></span>
      </div>
      <ul class="contact-list">
        <li>916-384-7702</li>
        <li>info@tlane-studio.example</li>
        <li>www.<span class="accent">tlane-studio</span>.example</li>
      </ul>
      <div class="contact-divider"></div>
      <p class="social"><span class="accent">IG:</span> @t.lanestudio</p>
    </div>
  </section>

  <section class="card card--logo" aria-label="Logo side">
    <div class="edge-tab edge-tab--left"></div>
    <div class="edge-tab edge-tab--right"></div>
    <div class="logo-body">
      <div class="brand">
        <span class="brand__name">T. Lane Studio</span>
        <span class="brand__dot"></span>
      </div>
    </div>
  </section>
</main>
</body>
</html>
```